Modern Business Card

Modern professional business card with more than just logo and demographic info. Something memorable.

We are a trendy/modern chiropractic group with an emphasis on neurology, hence the minimalist-type brain logo. We want to convey that modern and technical aspect with professionalism and the elite nature of our practice environment.

```html
<!DOCTYPE html>
<html lang="en">
<head>
<meta charset="utf-8">
<title>Northline Spine – Business Card</title>
<link href="https://fonts.googleapis.com/css2?family=Open+Sans:wght@300;400;700&family=Cinzel:wght@500&display=swap" rel="stylesheet">
<style>
  :root {
    --brand-blue: #4680c2;
    --ink: #1a1a1a;
    --paper: #ffffff;
    --backdrop: #4a4c50;
  }
  * { margin: 0; padding: 0; box-sizing: border-box; }
  html, body { width: 1200px; height: 900px; overflow: hidden; }
  body {
    background: var(--backdrop);
    font-family: "Open Sans", Arial, sans-serif;
    position: relative;
  }
  .card {
    position: absolute;
    left: 250px;
    width: 700px;
    height: 400px;
    background: var(--paper);
    border-radius: 18px;
    overflow: hidden;
  }
  .card-front { top: 40px; }
  .card-back { top: 470px; }

  /* Front */
  .front-band {
    position: absolute; left: 0; right: 0; top: 100px; height: 170px;
    background: var(--brand-blue);
    display: flex; align-items: center; justify-content: center;
  }
  .brand-name {
    font-family: "Cinzel", Georgia, serif;
    font-weight: 500;
    letter-spacing: 2px;
  }
  .front-band .brand-name { color: var(--paper); font-size: 46px; display: flex; align-items: center; gap: 16px; }
  .brand-square { width: 22px; height: 22px; background: currentColor; display: inline-block; }
  .front-web {
    position: absolute; left: 0; right: 0; top: 318px;
    display: flex; align-items: center; gap: 14px;
    color: var(--brand-blue); font-size: 17px; letter-spacing: 0.5px;
  }
  .front-web .rule { flex: 1; height: 2px; background: var(--brand-blue); }

  /* Back */
  .back-logo {
    position: absolute; right: 40px; top: 48px;
    color: var(--ink); font-size: 30px;
    display: flex; align-items: center; gap: 12px;
  }
  .back-logo .brand-square { background: var(--brand-blue); width: 20px; height: 20px; }
  .side-tab { position: absolute; left: 0; top: 170px; width: 14px; height: 48px; background: var(--brand-blue); }
  .person { position: absolute; left: 60px; top: 128px; }
  .person-name { font-size: 36px; color: var(--ink); line-height: 1; letter-spacing: -0.5px; }
  .person-name .first { font-weight: 700; }
  .person-name .last { font-weight: 300; }
  .person-role { font-size: 17px; font-weight: 400; color: var(--ink); margin-top: 4px; letter-spacing: 0.5px; }
  .divider-accent { position: absolute; left: 60px; top: 205px; width: 270px; height: 4px; background: var(--brand-blue); }
  .divider-line { position: absolute; left: 330px; top: 206px; width: 320px; height: 1.5px; background: var(--ink); }
  .contact { position: absolute; left: 90px; display: flex; align-items: center; gap: 16px; font-size: 18px; color: var(--ink); }
  .contact-phone { top: 245px; }
  .contact-web { top: 293px; left: 110px; }
  .icon-box { width: 30px; height: 30px; background: var(--brand-blue); border-radius: 3px; display: flex; align-items: center; justify-content: center; }
  .address { position: absolute; right: 50px; top: 228px; text-align: right; font-size: 16px; color: var(--ink); line-height: 1.35; }
  .address .icon-box { margin: 0 0 8px auto; width: 28px; height: 28px; }
  .bottom-band { position: absolute; left: 0; right: 0; bottom: 0; height: 34px; background: var(--brand-blue); }
</style>
</head>
<body>
  <section class="card card-front" aria-label="Card front">
    <div class="front-band">
      <span class="brand-name"><span class="brand-square"></span>Northline Spine</span>
    </div>
    <div class="front-web">
      <span class="rule"></span>
      <span>www.northlinespine.com</span>
      <span class="rule"></span>
    </div>
  </section>

  <section class="card card-back" aria-label="Card back">
    <div class="back-logo brand-name"><span class="brand-square"></span>Northline Spine</div>
    <div class="side-tab"></div>
    <div class="person">
      <div class="person-name"><span class="first">DANIEL</span> <span class="last">HARLOW</span></div>
      <div class="person-role">FOUNDER &amp; CEO</div>
    </div>
    <div class="divider-accent"></div>
    <div class="divider-line"></div>
    <div class="contact contact-phone">
      <span class="icon-box">
        <svg width="14" height="16" viewBox="0 0 14 16"><rect x="3" y="1" width="8" height="14" rx="1.5" fill="none" stroke="#fff" stroke-width="1.5"/><circle cx="7" cy="12" r="1" fill="#fff"/></svg>
      </span>
      <span>012-555-0143</span>
    </div>
    <div class="contact contact-web">
      <span class="icon-box">
        <svg width="16" height="16" viewBox="0 0 16 16"><circle cx="3" cy="13" r="1.6" fill="#fff"/><path d="M2 8a6 6 0 0 1 6 6M2 4a10 10 0 0 1 10 10" fill="none" stroke="#fff" stroke-width="1.6"/></svg>
      </span>
      <span>www.northlinespine.com</span>
    </div>
    <div class="address">
      <span class="icon-box">
        <svg width="12" height="16" viewBox="0 0 12 16"><path d="M6 15s5-5.5 5-9A5 5 0 0 0 1 6c0 3.5 5 9 5 9z" fill="#fff"/><circle cx="6" cy="6" r="1.8" fill="#4680c2"/></svg>
      </span>
      Address, Suit, Floor<br>City, Country, Zipcode
    </div>
    <div class="bottom-band"></div>
  </section>
</body>
</html>
```